Request for Business Card Design

Hi. My name is Marlene, I am looking for a new business card design for my company, Quarrow Signal Instruments, LLC. I really like the design you did for Tarsel Venture and was hoping you could do something similar using our full logo and our mark. I am also open to any raised texture design using our mark. I have attached our full logo, which would need to be somewhere on the card, as well as the mark in both outline and full form, as well as our brand colors / guide. The card does not have to be white, as long as our logo and mark appear. I actually like darker colored business cards more, but am open to all options. If you are interested in working with me, please let me know. We would also take the business card design into letterhead design if you can do that.

```html
<!DOCTYPE html>
<html lang="en">
<head>
<meta charset="utf-8">
<title>Quarrow Signal Instruments – Business Card</title>
<link href="https://fonts.googleapis.com/css2?family=Open+Sans:wght@400;600;700&display=swap" rel="stylesheet">
<style>
  :root {
    --backdrop: #2a2a2b;
    --card: #222327;
    --brand-blue: #1a9ac6;
    --text-light: #ffffff;
    --wordmark-faint: #3b3d41;
    --shadow: rgba(0, 0, 0, 0.55);
  }
  * { box-sizing: border-box; margin: 0; padding: 0; }
  html, body {
    width: 1200px; height: 780px; overflow: hidden;
    background: var(--backdrop);
    font-family: "Open Sans", Arial, sans-serif;
  }
  .canvas {
    position: relative; width: 1200px; height: 780px;
  }
  .card {
    position: absolute; width: 540px; height: 310px;
    background: var(--card);
    box-shadow: 0 14px 30px var(--shadow);
    overflow: hidden;
  }
  .card--front { left: 40px; top: 235px; }
  .card--back  { left: 620px; top: 235px; }

  /* Company name lockup */
  .brand { position: absolute; display: flex; align-items: center; gap: 14px; }
  .brand__dot { border-radius: 50%; background: var(--brand-blue); flex: none; }
  .brand__name {
    font-weight: 700; text-transform: uppercase; line-height: 1;
  }
  .brand__name span { display: block; }

  .card--front .brand { left: 70px; top: 118px; }
  .card--front .brand__dot { width: 58px; height: 58px; }
  .card--front .brand__name { color: var(--wordmark-faint); }
  .card--front .brand__main { font-size: 46px; letter-spacing: 5px; }
  .card--front .brand__sub { font-size: 12.5px; letter-spacing: 1.6px; margin-top: 6px; }

  .card--back .brand { left: 34px; top: 34px; }
  .card--back .brand__dot { width: 40px; height: 40px; }
  .card--back .brand__name { color: var(--text-light); }
  .card--back .brand__main { font-size: 30px; letter-spacing: 3px; }
  .card--back .brand__sub { font-size: 8.4px; letter-spacing: 1.1px; margin-top: 4px; }

  /* Person */
  .person { position: absolute; right: 44px; top: 44px; text-align: right; }
  .person__name { color: var(--brand-blue); font-weight: 700; font-size: 34px; line-height: 1; }
  .person__role { color: var(--text-light); font-size: 13px; font-weight: 600; margin-top: 4px; }
  .accent-bar {
    position: absolute; right: 0; top: 44px; width: 22px; height: 56px;
    background: var(--brand-blue);
  }

  /* Address & contacts */
  .address {
    position: absolute; left: 44px; top: 150px;
    color: var(--text-light); font-size: 13.5px; line-height: 1.35; font-style: normal;
  }
  .contacts {
    position: absolute; left: 44px; top: 208px; list-style: none;
    color: var(--text-light); font-size: 13px; line-height: 1;
  }
  .contacts li { display: flex; align-items: center; gap: 9px; height: 21px; }
  .contacts svg { width: 13px; height: 13px; fill: var(--brand-blue); flex: none; }
</style>
</head>
<body>
<main class="canvas">

  <section class="card card--front" aria-label="Card front">
    <div class="brand">
      <span class="brand__dot"></span>
      <p class="brand__name">
        <span class="brand__main">Quarrow</span>
        <span class="brand__sub">Signal Instruments</span>
      </p>
    </div>
  </section>

  <section class="card card--back" aria-label="Card back">
    <div class="brand">
      <span class="brand__dot"></span>
      <p class="brand__name">
        <span class="brand__main">Quarrow</span>
        <span class="brand__sub">Signal Instruments</span>
      </p>
    </div>

    <div class="person">
      <p class="person__name">Marlene</p>
      <p class="person__role">Director</p>
    </div>
    <span class="accent-bar"></span>

    <address class="address">
      1180 Fenwick Park Road<br>
      Alder Springs, CO 80671
    </address>

    <ul class="contacts">
      <li>
        <svg viewBox="0 0 24 24" aria-hidden="true"><path d="M6.6 10.8a15.1 15.1 0 0 0 6.6 6.6l2.2-2.2a1 1 0 0 1 1-.25 11.4 11.4 0 0 0 3.6.57 1 1 0 0 1 1 1V20a1 1 0 0 1-1 1A17 17 0 0 1 3 4a1 1 0 0 1 1-1h3.5a1 1 0 0 1 1 1c0 1.25.2 2.45.57 3.57a1 1 0 0 1-.25 1z"/></svg>
        +001 555 218 4730
      </li>
      <li>
        <svg viewBox="0 0 24 24" aria-hidden="true"><path d="M6 2h9l3 3v5H6z M3 11h18v10H3z M6 14h3v2H6z M11 14h3v2h-3z M16 14h3v2h-3z"/></svg>
        +001 555 218 4731
      </li>
      <li>
        <svg viewBox="0 0 24 24" aria-hidden="true"><path d="M12 2a10 10 0 1 0 0 20 10 10 0 0 0 0-20zm-1 17.9A8 8 0 0 1 4.2 10.2L9 15v1a2 2 0 0 0 2 2zm6.9-2.5A2 2 0 0 0 16 16h-1v-3a1 1 0 0 0-1-1H8v-2h2a1 1 0 0 0 1-1V7h2a2 2 0 0 0 2-2v-.4a8 8 0 0 1 2.9 12.8z"/></svg>
        www.quarrowsignal.com
      </li>
      <li>
        <svg viewBox="0 0 24 24" aria-hidden="true"><path d="M2 5h20v14H2z M3.5 6.5 12 13l8.5-6.5v1.8L12 15 3.5 8.3z" fill-rule="evenodd"/></svg>
        info@quarrowsignal.com
      </li>
    </ul>
  </section>

</main>
</body>
</html>
```